Single-sided business card for restaurant velmora with new logo made on this site

Business card options with new logo including restaurant name, address, phone number and website. This business card is single-sided only and will be presented at the hostess desk for clients to take. I would like to see options based on a cream card background, a white card background, a yellow card background and a burgundy colored background. It needs to be elegant and traditional.

Target Market(s)

local and international crowd

Industry/Entity Type

restaurant

Contact Information for Business Card

address, website and phone number

Font styles to use
Serif

Colors
EE7325
F08F49
F5BC92
FAE3D3
FDF4ED

Requirements
Must have
• new logo, address, phone number, website
Should not have
• more than three colors

```html
<!DOCTYPE html>
<html lang="es">
<head>
<meta charset="utf-8">
<title>Velmora – Tarjeta de presentación</title>
<link href="https://fonts.googleapis.com/css2?family=Cinzel:wght@400;500&family=Arimo:wght@400&display=swap" rel="stylesheet">
<style>
  :root {
    --backdrop: #2b2b2b;
    --card: #ffffff;
    --ink: #3b1a1d;
    --gold: #f2ac2e;
  }
  html, body {
    margin: 0;
    width: 1200px;
    height: 1015px;
    overflow: hidden;
    background: var(--backdrop);
  }
  .business-card {
    position: absolute;
    left: 150px;
    top: 250px;
    width: 900px;
    height: 515px;
    background: var(--card);
    box-shadow: 0 12px 30px rgba(0,0,0,0.5);
  }
  .brand {
    position: absolute;
    right: 90px;
    top: 60px;
    width: 300px;
    text-align: center;
  }
  .brand-square {
    display: block;
    width: 120px;
    height: 120px;
    margin: 0 auto 22px;
    background: var(--gold);
  }
  .brand-name {
    font-family: "Cinzel", serif;
    font-weight: 500;
    font-size: 44px;
    letter-spacing: 10px;
    color: var(--ink);
    line-height: 1;
  }
  .rule {
    position: absolute;
    height: 1.5px;
    background: var(--gold);
  }
  .rule-brand { left: 520px; right: 50px; top: 268px; }
  .rule-reservations { left: 190px; right: 50px; top: 400px; }
  .website {
    position: absolute;
    left: 70px;
    top: 190px;
    font-family: "Arimo", sans-serif;
    font-size: 22px;
    letter-spacing: 0.5px;
    color: var(--ink);
  }
  .website-name { color: var(--gold); }
  .reservations {
    position: absolute;
    left: 190px;
    top: 348px;
    font-family: "Cinzel", serif;
    font-size: 34px;
    letter-spacing: 1.5px;
    color: var(--ink);
    white-space: nowrap;
  }
  .address {
    position: absolute;
    left: 205px;
    top: 418px;
    font-family: "Arimo", sans-serif;
    font-size: 22px;
    line-height: 30px;
    color: var(--ink);
  }
  .address p { margin: 0; }
</style>
</head>
<body>
  <div class="business-card">
    <div class="brand">
      <span class="brand-square"></span>
      <div class="brand-name">VELMORA</div>
    </div>
    <div class="rule rule-brand"></div>

    <div class="website">www.<span class="website-name">velmora</span>.com.mx</div>

    <div class="reservations">RESERVACIONES 958-555-0142</div>
    <div class="rule rule-reservations"></div>

    <div class="address">
      <p>Restaurant Velmora, Azucena 418</p>
      <p>Bahías de Cantelo, Oaxaca CP 70950</p>
    </div>
  </div>
</body>
</html>
```